Mobile Fitness snd Therapy Business Card Design

I need a business card designed for my mobile fitness and therapy business.

Please view the images that I have uploaded. I like the simplicity of the design that I have attached. I adapted it with my information

Target Market(s)

Those seeking personal training, injury rehabilitation or massage therapy.

Industry/Entity Type

Business

Contact Information for Business Card

Derek Fulham - MSc, CAT(C), RMT, CSCS, Pn2
e-mail: derek@vantrelo.com
website: www.vantrelo.com
instagram: @derek_fulham

Font styles to use
Sans Serif

Colors
3176b5
0355a3

Requirements
Must have
• "Contact us to receive a FREE assessment"
• Services offered:
• Personal Training
• Golf Fitness
• Injury Rehab
• Massage Therapy
• Yoga
Nice to have
• Consistent colours with brand
• - Dark Blue: #232837
• - Blue: #5096f0
• Consistent look/feel with the website: www.vantrelo.com

```html
<!DOCTYPE html>
<html lang="en">
<head>
<meta charset="utf-8">
<title>Vantrelo Business Card</title>
<link rel="stylesheet" href="https://fonts.googleapis.com/css2?family=Montserrat:wght@700&family=Roboto:wght@400&family=Roboto+Condensed:wght@700&display=swap">
<style>
  :root {
    --page: #e9e9eb;
    --card-front: #f7f7f7;
    --navy: #222838;
    --blue: #2a5bd7;
    --blue-light: #8dbdf8;
    --text-grey: #444a55;
    --white: #ffffff;
  }
  html, body {
    margin: 0;
    width: 1200px;
    height: 960px;
    overflow: hidden;
    background: var(--page);
  }
  .card {
    position: absolute;
    width: 600px;
    height: 343px;
    border-radius: 18px;
    box-sizing: border-box;
  }
  .card-front { left: 315px; top: 113px; background: var(--card-front); }
  .card-back { left: 312px; top: 473px; background: var(--navy); }

  .brand-name {
    font-family: "Montserrat", sans-serif;
    font-weight: 700;
    letter-spacing: 2px;
    line-height: 1;
    margin: 0;
  }
  .brand-tagline {
    font-family: "Montserrat", sans-serif;
    font-weight: 700;
    letter-spacing: 2px;
    line-height: 1;
    margin: 0;
  }

  .front-brand {
    position: absolute;
    right: 38px;
    top: 40px;
    text-align: right;
    color: var(--navy);
  }
  .front-brand .brand-name { font-size: 38px; }
  .front-brand .brand-tagline { font-size: 12.5px; margin-top: 8px; }

  .person {
    position: absolute;
    right: 38px;
    top: 188px;
    text-align: right;
    color: var(--blue);
    font-family: "Roboto Condensed", sans-serif;
    font-weight: 700;
  }
  .person-name { font-size: 22px; line-height: 1; margin: 0; }
  .person-credentials { font-size: 11px; margin: 4px 0 0; }

  .contact-list {
    position: absolute;
    right: 38px;
    top: 246px;
    list-style: none;
    margin: 0;
    padding: 0;
    font-family: "Roboto", sans-serif;
    font-size: 14px;
    color: var(--text-grey);
    text-align: right;
  }
  .contact-list li {
    display: flex;
    justify-content: flex-end;
    align-items: center;
    gap: 6px;
    height: 20px;
  }
  .contact-icon { width: 13px; height: 13px; flex: none; }

  .back-brand {
    position: absolute;
    left: 0;
    right: 0;
    top: 130px;
    text-align: center;
    color: var(--white);
  }
  .back-brand .brand-name { font-size: 44px; }
  .back-brand .brand-tagline { font-size: 15px; margin-top: 12px; }

  .offer {
    position: absolute;
    left: 57px;
    top: 256px;
    width: 484px;
    height: 34px;
    border-radius: 17px;
    background: var(--blue);
    color: var(--white);
    font-family: "Roboto Condensed", sans-serif;
    font-weight: 700;
    font-size: 20px;
    line-height: 34px;
    text-align: center;
  }
  .services {
    position: absolute;
    left: 0;
    right: 0;
    top: 296px;
    text-align: center;
    font-family: "Roboto", sans-serif;
    font-size: 14.5px;
    color: var(--white);
  }
  .services .sep { color: var(--blue-light); opacity: .7; margin: 0 3px; }
</style>
</head>
<body>
  <section class="card card-front">
    <div class="front-brand">
      <p class="brand-name">VANTRELO</p>
      <p class="brand-tagline">NUTRITION - FITNESS - HEALTH</p>
    </div>
    <div class="person">
      <p class="person-name">DEREK FULHAM</p>
      <p class="person-credentials">MSC, CAT(C), RMT, CSCS, PN2</p>
    </div>
    <ul class="contact-list">
      <li>derek@vantrelo.com
        <svg class="contact-icon" viewBox="0 0 13 13" aria-hidden="true"><rect x="1" y="3" width="11" height="8" rx="1" fill="var(--blue)"/><path d="M1.5 3.5 6.5 7.5 11.5 3.5" fill="none" stroke="#fff" stroke-width="1"/></svg>
      </li>
      <li>www.vantrelo.com
        <svg class="contact-icon" viewBox="0 0 13 13" aria-hidden="true"><circle cx="6.5" cy="6.5" r="6" fill="var(--blue)"/><ellipse cx="6.5" cy="6.5" rx="2.5" ry="5.5" fill="none" stroke="#fff" stroke-width=".8"/><path d="M1 6.5h11" stroke="#fff" stroke-width=".8"/></svg>
      </li>
      <li>@derek_fulham
        <svg class="contact-icon" viewBox="0 0 13 13" aria-hidden="true"><circle cx="6.5" cy="6.5" r="6" fill="var(--blue)"/></svg>
      </li>
    </ul>
  </section>

  <section class="card card-back">
    <div class="back-brand">
      <p class="brand-name">VANTRELO</p>
      <p class="brand-tagline">NUTRITION - FITNESS - HEALTH</p>
    </div>
    <div class="offer">CONTACT US TO RECEIVE A FREE ASSESSMENT</div>
    <div class="services">Personal Training<span class="sep">|</span>Golf Fitness<span class="sep">|</span>Injury Rehab<span class="sep">|</span>Massage Therapy<span class="sep">|</span>Yoga</div>
  </section>
</body>
</html>
```